Wine Label Design-Hollow Creek Vineyard

Hollow Creek Vineyard is in the Barossa Valley in South Australia. The Barossa is recognized as Australia's premier wine region, producing Australia's icon wines and some " new takes on traditional".
This family owned and operated vineyard grows some exceptionally high quality fruit. Most of the fruit is sold and used for some of Australia's most iconic wines. Small quantities are retained by the owners for some wines with very limited availability. (Wines were previously sold as Brackwell Vineyards Hollow Creek ( Shiraz, Cabernet etc).

The wines will in the future be labeled simply ‘Hollow Creek Vineyard’. The label will launch this new identity for the single family single vineyard and its high quality wines which are a true expression of the vineyard and derive from the Hollow Creek common to this ancient area (800-2000 million years old).
The label should reflect
• Single vineyard, family owned
• vines in very old rock & soils
• High quality & reliability
• Edgy but true, design based thinking (Please note:blue is generally seen as an unacceptable colour for a wine label?? Don’t ask me why)

The wines will be sold mostly direct in Australia ( ie not through retail stores), with limited export to Asia, Scandinavia and Canada.
There are three quality levels and price points in the portfolio
1. Entry level premium for everyday drinking for discriminating drinkers-approx AUD20
2. Super Premium-approx AUD30
3. Limited Release ultlra premium-AUD75-90?
We envisage three variations on the label but with an obvious & common design element. This design element should be able to be used for corporate identification and promotion
The paper stock will be waterproof and self adhesive. Our preference is for designs that engage the user by appealing to both sight and touch. It is preferred that textures be added eg embossing, high build varnish etc-rather than be a facet of the stock itself.
For information on statutory label requirements refer to www.vintnerregistry-example.com . In brief
o Front label need not show any mandatory information. However we would prefer Variety, Barossa Valley, Year and alcohol to be shown on the front label
o Back label should show all mandatories and allow for a bar code
Updates

Project Deadline Extended
Reason: I've had a problem with my wireless broadband account and reception has been intermittent to say the least to the extent that I switched off at the weekend. Just going downtown now for a 'polite discussion' with my service provider.

Project Deadline Extended
Reason: I have receiver insufficient designs of quality which we would consider. Too many designs have a "cut and paste" appearance - too few exhibit an original art/design element which truly identifies the product.

Gals & Guys

most of the designs submitted lack punch and originality and are totally unmemorable.
Please-get on Searcho or whatever enter "Wine Label Designs" and do some research b4 u waste your time and mine. Formulaic cut and paste will not win the day. That's not to say that cut and paste can't work-but it must have some originality, impact and command attention. Please surprise me.

Following on from a question from a designer about who is our competition and what we are looking for I sent the following 
"I don't think I can add anything new. Read the brief and comments again and research wine labels on the web. In 30 minutes you'll get a good idea of the creative edgy designs in the industry. There are a plethora of collections. Our competition-anyone with a label. In 2010 there were over 2400 "producers" in other words 2400 producers with at least one label. In fact there are over 25000 Australian wines and then the numerous imported wines.

Target Market(s)

$20 people who budget everyday but have graduated from drinking 'entry level' wines. These people will likely fit into Cat. (b) in the $30 wine

$30 (a) will not over-compromise on some everyday discretionary expenditure.(b) might buy for special occasions

$70-$90 Professional/successful people with high disposable/discretionary income not particularly worried about recession. wine geeks.

Industry/Entity Type

Retail

Requirements
Must have
• identifiable element across range of wines

```html
<!DOCTYPE html>
<html lang="en">
<head>
<meta charset="utf-8">
<title>Hollow Creek Vineyard — Wine Labels</title>
<link rel="stylesheet" href="https://fonts.googleapis.com/css2?family=Open+Sans:wght@300;400;700&display=swap">
<style>
  :root {
    --canvas: #c8c9cc;
    --label-white: #f7f7f7;
    --label-white-edge: #e6e6e6;
    --label-stone: #e3e0d3;
    --label-stone-edge: #d6d3c4;
    --ink: #5a5a5a;
    --ink-soft: #8a8a8a;
    --green-main: #86ad45;
    --green-deep: #5e8c3c;
    --green-light: #c3cf4a;
    --red-main: #b9452c;
    --red-deep: #8f1f1e;
    --red-light: #cfa95e;
    --stone-main: #a9a594;
    --stone-deep: #767a6c;
    --stone-light: #ffffff;
  }
  * { box-sizing: border-box; margin: 0; padding: 0; }
  html, body {
    width: 1200px; height: 900px; overflow: hidden;
    background: var(--canvas);
    font-family: "Open Sans", Arial, sans-serif;
  }
  .label-range {
    position: relative; width: 1200px; height: 900px;
  }
  .label {
    position: absolute; top: 203px; width: 322px; height: 494px;
    background: linear-gradient(90deg, var(--label-white-edge) 0%, var(--label-white) 18%, var(--label-white) 82%, var(--label-white-edge) 100%);
  }
  .label--entry { left: 40px; }
  .label--super { left: 440px; }
  .label--limited {
    left: 840px;
    background: linear-gradient(90deg, var(--label-stone-edge) 0%, var(--label-stone) 18%, var(--label-stone) 82%, var(--label-stone-edge) 100%);
  }
  .rock-art {
    position: absolute; left: 20px; top: 48px; width: 282px; height: 250px;
    border-radius: 40%;
  }
  .label--entry .rock-art {
    background: radial-gradient(ellipse at 50% 45%, var(--green-main) 0%, var(--green-deep) 35%, var(--green-light) 55%, rgba(247,247,247,0) 72%);
  }
  .label--super .rock-art {
    background: radial-gradient(ellipse at 50% 45%, var(--red-main) 0%, var(--red-deep) 35%, var(--red-light) 55%, rgba(247,247,247,0) 72%);
  }
  .label--limited .rock-art {
    background: radial-gradient(ellipse at 50% 45%, var(--stone-main) 0%, var(--stone-deep) 35%, var(--stone-light) 55%, rgba(227,224,211,0) 72%);
  }
  .brand {
    position: absolute; left: 38px; top: 326px;
    display: flex; align-items: center; gap: 14px;
  }
  .brand-dot { width: 48px; height: 48px; border-radius: 50%; flex: none; }
  .label--entry .brand-dot { background: var(--green-main); }
  .label--super .brand-dot { background: var(--red-deep); }
  .label--limited .brand-dot { background: #5c5c5c; }
  .brand-name {
    font-weight: 400; color: var(--ink);
    font-size: 26px; line-height: 25px; letter-spacing: -0.5px;
  }
  .brand-name span { display: block; }
  .brand-name .brand-sub { font-size: 15px; line-height: 18px; letter-spacing: 0; }
  .wine-details {
    position: absolute; left: 100px; top: 430px; width: 200px;
    color: var(--ink-soft); font-size: 12px; line-height: 12px;
  }
  .region { display: block; font-weight: 400; }
  .variety { display: block; font-weight: 700; font-size: 11px; color: var(--ink); }
  .vintage-info { position: absolute; left: 142px; top: 0; }
  .vintage { display: block; font-weight: 700; font-size: 11px; color: var(--ink); }
  .alcohol { display: block; font-size: 7px; line-height: 9px; }
</style>
</head>
<body>
<main class="label-range">
  <section class="label label--entry">
    <div class="rock-art" role="img" aria-label="Stacked faceted rock slabs in greens and lime, floating above a soft shadow"></div>
    <div class="brand">
      <div class="brand-dot"></div>
      <p class="brand-name"><span>HOLLOW</span><span>CREEK</span><span class="brand-sub">VINEYARDS</span></p>
    </div>
    <div class="wine-details">
      <span class="region">BAROSSA VALLEY</span>
      <span class="variety">SHIRAZ</span>
      <div class="vintage-info"><span class="vintage">2012</span><span class="alcohol">13,5 ALC VOL.</span></div>
    </div>
  </section>

  <section class="label label--super">
    <div class="rock-art" role="img" aria-label="Stacked faceted rock slabs in reds, terracotta and ochre, floating above a soft shadow"></div>
    <div class="brand">
      <div class="brand-dot"></div>
      <p class="brand-name"><span>HOLLOW</span><span>CREEK</span><span class="brand-sub">VINEYARDS</span></p>
    </div>
    <div class="wine-details">
      <span class="region">BAROSSA VALLEY</span>
      <span class="variety">SHIRAZ</span>
      <div class="vintage-info"><span class="vintage">2012</span><span class="alcohol">13,5 ALC VOL.</span></div>
    </div>
  </section>

  <section class="label label--limited">
    <div class="rock-art" role="img" aria-label="Stacked faceted rock slabs in white, stone and slate grey, floating above a soft shadow"></div>
    <div class="brand">
      <div class="brand-dot"></div>
      <p class="brand-name"><span>HOLLOW</span><span>CREEK</span><span class="brand-sub">VINEYARDS</span></p>
    </div>
    <div class="wine-details">
      <span class="region">BAROSSA VALLEY</span>
      <span class="variety">SHIRAZ</span>
      <div class="vintage-info"><span class="vintage">2012</span><span class="alcohol">13,5 ALC VOL.</span></div>
    </div>
  </section>
</main>
</body>
</html>
```